Hi,

Here are some thoughts on the book cover for The BRIGHT Vitality Map: A Restorative Wellness Path for Active Mothers and their Households.

To simplify this project I've uploaded some images (all images are of a vortex or swirl) that I would like to see the book cover design created with. I've also uploaded a set of "elements" that I would like to see incorporated into the vortex.

My vision is to have you infuse the smaller "elements" into the vortex so they look like they are caught in the vortex or swirling in the vortex.

I have upload an amateur example which I did but it shows the smaller elements dropped into the larger vortex image.

Please don't hesitate to write me with any questions you may have.

Thank you,

Gareth

Please.

Target Market(s)

Busy Women, both stay at home and career women

Industry/Entity Type

Health

Font styles to use
Serif
Sans Serif

Requirements
Must have
• vortex or swirl with circular elements infused

```html
<!DOCTYPE html>
<html lang="en">
<head>
<meta charset="utf-8">
<title>The BRIGHT Vitality Map — Book Cover</title>
<link rel="stylesheet" href="https://fonts.googleapis.com/css2?family=Oswald:wght@400;500&family=Libre+Baskerville&family=Lato:wght@400&display=swap">
<style>
  :root {
    --bg-centre: #fbfbe6;
    --bg-mid: #d9eca0;
    --bg-edge: #a9d04c;
    --title-pink: #ea1a6c;
    --title-blue: #1b8fd2;
    --subtitle-teal: #1f5d68;
    --band-teal: #1ba597;
    --author-white: #ffffff;
  }
  html, body {
    margin: 0;
    padding: 0;
    overflow: hidden;
    background: #ffffff;
  }
  .cover {
    position: relative;
    width: 800px;
    height: 1200px;
    overflow: hidden;
    background: radial-gradient(ellipse 560px 640px at 400px 430px,
      var(--bg-centre) 0%, var(--bg-mid) 45%, var(--bg-edge) 100%);
  }
  .swirl-emblem {
    position: absolute;
    left: 318px;
    top: 40px;
    width: 172px;
    height: 480px;
    border-radius: 86px;
    background: linear-gradient(180deg, #a2325e 0%, #ee3d6e 22%, #f2705a 38%, #c9973a 55%, #8cc43f 72%, #3fbf8c 100%);
    opacity: 0.9;
  }
  .emblem-shadow {
    position: absolute;
    left: 310px;
    top: 528px;
    width: 180px;
    height: 24px;
    border-radius: 50%;
    background: radial-gradient(ellipse at center, rgba(60,70,40,0.35) 0%, rgba(60,70,40,0) 70%);
  }
  .title {
    position: absolute;
    left: 0;
    top: 540px;
    width: 800px;
    margin: 0;
    text-align: center;
    font-family: "Oswald", sans-serif;
    font-weight: 500;
    text-transform: uppercase;
    line-height: 1;
  }
  .title-line {
    display: block;
    font-size: 112px;
    letter-spacing: 1px;
  }
  .title-line--pink { color: var(--title-pink); }
  .title-line--blue { color: var(--title-blue); margin-top: 6px; }
  .subtitle {
    position: absolute;
    left: 0;
    top: 782px;
    width: 800px;
    margin: 0;
    text-align: center;
    font-family: "Libre Baskerville", serif;
    font-variant: small-caps;
    font-size: 44px;
    line-height: 46px;
    letter-spacing: 1px;
    color: var(--subtitle-teal);
  }
  .author-band {
    position: absolute;
    left: 0;
    top: 1056px;
    width: 800px;
    height: 144px;
    background: var(--band-teal);
    display: flex;
    align-items: center;
    justify-content: center;
  }
  .author-name {
    font-family: "Lato", sans-serif;
    font-weight: 400;
    font-size: 56px;
    letter-spacing: 14px;
    padding-left: 14px;
    color: var(--author-white);
    text-transform: uppercase;
  }
</style>
</head>
<body>
  <div class="cover">
    <div class="swirl-emblem" role="img" aria-label="Twisting ribbon swirl emblem in plum, coral, amber and green tones"></div>
    <div class="emblem-shadow"></div>

    <h1 class="title">
      <span class="title-line title-line--pink">The Bright</span>
      <span class="title-line title-line--blue">Vitality Map</span>
    </h1>

    <p class="subtitle">A Restorative Wellness Path<br>for Active Mothers<br>and their Households</p>

    <div class="author-band">
      <span class="author-name">Gareth</span>
    </div>
  </div>
</body>
</html>
```